Brisk Fixwell business card

I need business card for my business, I think you have all my details.six months ago I design with you car wrap design. We would like to design both side of the card. On front of card we would like logo , Name and our contact details.
At the back we are looking to mentioned our services.
The name will be:
Faridoullan Mestor
Managing Director
Ph:07952338417
Email:info@brisk-fixwell.com
Web:www.brisk-fixwell.com
So we have our logo, you don’t need to change the logo.
Please see the attachment.
Thanks

Target Market(s)

Home improvement

Industry/Entity Type

Home Improvement

Contact Information for Business Card

Company name: Brisk Fixwell
Name: Faridoullan Mestor
Position: Director
Ph:07952338417
Web: www.brisk-fixwell.com
Add: 42 Corvale Road
Larkford
TW3 9KD
SECOND PERSON
Nizamuddel mestor
Position: Handyman
Ph: 07812 564037
Email: info@brisk-fixwell.com
Add: 18 Brackwin Lane Road
Larkford
TW6 2LB

```html
<!DOCTYPE html>
<html lang="en">
<head>
<meta charset="utf-8">
<title>Brisk Fixwell business card</title>
<link rel="stylesheet" href="https://fonts.googleapis.com/css2?family=Open+Sans:wght@400;600;700&display=swap">
<style>
  :root {
    --navy: #253a85;
    --navy-deep: #1f2f6e;
    --red: #e0262b;
    --grey-text: #555b66;
    --grey-bar: #a7a9ac;
    --paper: #ffffff;
    --backdrop: #d9d9d9;
  }
  * { box-sizing: border-box; margin: 0; padding: 0; }
  html, body { width: 1200px; height: 801px; overflow: hidden; }
  body {
    background: var(--backdrop);
    font-family: "Open Sans", Arial, sans-serif;
    display: flex;
    align-items: center;
    justify-content: center;
    gap: 40px;
  }
  .card {
    width: 560px;
    height: 320px;
    position: relative;
    overflow: hidden;
  }
  .card--front {
    background: var(--paper);
    border-bottom: 3px solid var(--navy);
  }
  .card--back { background: var(--navy); }

  .brand {
    position: absolute;
    display: flex;
    align-items: center;
    gap: 10px;
    font-weight: 700;
    white-space: nowrap;
  }
  .brand__mark { display: block; flex: none; }
  .card--front .brand {
    left: 34px; top: 142px;
    font-size: 26px;
    color: var(--navy);
  }
  .card--front .brand__mark { width: 20px; height: 20px; background: var(--red); }
  .card--back .brand {
    left: 56px; bottom: 56px;
    font-size: 44px;
    color: var(--paper);
  }
  .card--back .brand__mark { width: 34px; height: 34px; background: var(--grey-bar); }

  .divider {
    position: absolute;
    left: 268px; top: 60px;
    width: 1px; height: 200px;
    background: var(--navy);
  }
  .contact {
    position: absolute;
    left: 288px; top: 62px;
    color: var(--grey-text);
    font-size: 14px;
    line-height: 1.45;
  }
  .contact__name {
    color: var(--navy);
    font-weight: 700;
    font-size: 21px;
    line-height: 1.2;
  }
  .contact__role { font-size: 14px; margin-bottom: 10px; }
  .contact__address { margin-bottom: 10px; }
  .contact__line { display: flex; align-items: center; gap: 8px; }
  .contact__icon { width: 11px; height: 11px; flex: none; }
</style>
</head>
<body>
  <section class="card card--front" aria-label="Card front">
    <div class="brand"><span class="brand__mark"></span>Brisk Fixwell</div>
    <div class="divider"></div>
    <div class="contact">
      <p class="contact__name">Faridoullan Mestor</p>
      <p class="contact__role">Director</p>
      <p class="contact__address">42 Corvale Road<br>Larkford, TW3 9KD</p>
      <p class="contact__line">
        <svg class="contact__icon" viewBox="0 0 12 12" aria-hidden="true"><path fill="#e0262b" d="M2.5 0.8 4.6 3 3.5 4.3c.7 1.6 2 2.9 3.6 3.7l1.3-1.1 2.2 2.1-1.3 1.9C5 10.5 1.2 6.7 0.6 2.1z"/></svg>
        07952338417
      </p>
      <p class="contact__line">
        <svg class="contact__icon" viewBox="0 0 12 12" aria-hidden="true"><rect x="0.5" y="2" width="11" height="8" fill="#e0262b"/><path d="M0.8 2.4 6 6.5l5.2-4.1" fill="none" stroke="#fff" stroke-width="1"/></svg>
        info@brisk-fixwell.com
      </p>
      <p class="contact__line">
        <svg class="contact__icon" viewBox="0 0 12 12" aria-hidden="true"><circle cx="6" cy="6" r="5.5" fill="#e0262b"/><path d="M0.8 6h10.4M6 0.6c-2.4 2.8-2.4 8 0 10.8M6 0.6c2.4 2.8 2.4 8 0 10.8" fill="none" stroke="#fff" stroke-width="0.9"/></svg>
        www.brisk-fixwell.com
      </p>
    </div>
  </section>

  <section class="card card--back" aria-label="Card back">
    <div class="brand"><span class="brand__mark"></span>Brisk Fixwell</div>
  </section>
</body>
</html>
```